Bright Nook Home Page (A Home Wellness e-commerce site & blog)

We need a dynamic home page created for a home wellness brand. Must be visually appealing and extremely mobile-friendly. Logos and a Navmap have been provided but that is just a guideline, PLEASE USE YOUR CREATIVITY.

Target Market(s)

1st target demo: females 24-48, 2nd target demo: all 24-48

Number of Pages Required

1 page

```html
<!DOCTYPE html>
<html lang="en">
<head>
<meta charset="utf-8">
<title>Bright Nook — Home Wellness</title>
<link rel="stylesheet" href="https://fonts.googleapis.com/css2?family=Jost:wght@400;500;600;700&family=Questrial&display=swap">
<style>
:root{
  --teal:#35bfc8;
  --purple:#5b2d91;
  --purple-soft:rgba(196,170,228,.62);
  --ink:#231f20;
  --grey-bg:#f2f2f2;
  --line:#8a8a8a;
  --white:#ffffff;
  --text:#222;
}
*{box-sizing:border-box;margin:0;padding:0}
html,body{width:1200px;height:4313px;overflow:hidden}
body{position:relative;background:var(--white);font-family:"Questrial",sans-serif;color:var(--text)}
.abs{position:absolute}
a{color:inherit;text-decoration:none}

/* top bar */
.topbar{left:0;top:0;width:1200px;height:47px;background:var(--teal);color:var(--white);font-size:12px}
.topbar .promo{left:172px;top:16px}
.social{display:flex;gap:13px}
.social span{width:22px;height:22px;border-radius:50%;background:var(--white);display:block}
.topbar .social{left:899px;top:12px}

/* nav */
.nav{left:0;top:47px;width:1200px;height:109px;background:var(--purple);color:var(--white)}
.brand{font-family:"Jost",sans-serif;font-weight:500;color:var(--white);letter-spacing:.5px}
.nav .brand{left:172px;top:26px;font-size:40px}
.menu{left:490px;top:46px;display:flex;gap:21px;font-size:13px;font-family:"Jost",sans-serif}
.menu .active{position:relative}
.menu .active::after{content:"";position:absolute;left:-2px;top:22px;width:40px;height:14px;border-bottom:4px solid var(--teal);border-radius:0 0 30px 30px}
.cart{left:976px;top:30px}

/* hero */
.hero{left:0;top:156px;width:1200px;height:740px}
.hero > svg{position:absolute;left:0;top:0}
.hero-badge{left:155px;top:71px;width:394px;height:394px;border-radius:50%;background:var(--purple-soft)}
.hero-title{left:172px;top:170px;font-family:"Jost",sans-serif;font-weight:600;font-size:50px;color:var(--purple)}
.btn{display:inline-flex;align-items:center;justify-content:center;border-radius:30px;color:var(--white);font-family:"Jost",sans-serif;font-weight:500}
.hero .shop{left:263px;top:276px;width:149px;height:60px;background:var(--teal);font-size:19px}
.dots{left:302px;top:390px;display:flex;gap:9px}
.dots span{width:16px;height:16px;border-radius:50%;background:#a796c9}
.dots span:first-child{background:var(--purple)}

/* sale banner */
.sale{left:172px;top:966px;width:854px;height:147px;border-radius:12px;background:linear-gradient(90deg,#ececec,#f4f4f4 50%,#e9e9e9);overflow:hidden}
.sale .thumb{left:0;top:0;width:165px;height:147px;background:linear-gradient(135deg,#cfd6c9,#e8d9dc 55%,#efefef)}
.sale p{left:196px;top:39px;width:640px;font-family:"Jost",sans-serif;font-weight:500;font-size:23px;line-height:35px;color:var(--purple);text-indent:-12px;padding-left:12px}

/* key heading */
.key-title{left:0;top:1200px;width:1200px;text-align:center;font-family:"Jost",sans-serif;font-weight:500;font-size:28px;line-height:44px;color:var(--purple)}

/* products */
.card{border:1px solid #555;border-radius:10px;background:var(--white);overflow:hidden}
.card .pic{position:absolute;left:30px;top:40px;right:30px;height:180px;border-radius:50%;background:radial-gradient(ellipse at center,#efe4d2 0%,#f7f1e8 45%,#ffffff 72%)}
.card .label{position:absolute;left:0;width:100%;text-align:center;font-family:"Jost",sans-serif;font-size:18px;color:#111}
.feature{border-radius:10px;overflow:hidden;border:1px solid #555}
.feature .copy{position:absolute;left:20px;color:var(--white)}
.feature .copy h3{font-family:"Jost",sans-serif;font-weight:400;font-size:18px}
.feature .copy p{font-size:15px;margin-top:6px}

/* about */
.about{left:0;top:2087px;width:1200px;height:486px;background:var(--grey-bg)}
.about h2{left:172px;top:105px;font-family:"Jost",sans-serif;font-weight:600;font-size:30px;color:var(--purple)}
.about p{left:172px;top:158px;width:480px;font-size:12.5px;line-height:28.5px;color:#333}
.about .tell{left:172px;top:325px;width:136px;height:52px;background:var(--purple);font-size:16px}
.about .pic{left:678px;top:56px;width:477px;height:368px;border-radius:45%;background:radial-gradient(ellipse at 45% 50%,#e9c89a 0%,#d8e2c8 40%,#eef1ea 70%,var(--grey-bg) 100%)}

/* pay later */
.pay-name{left:172px;top:2672px;font-family:"Jost",sans-serif;font-weight:500;font-size:64px;line-height:76px;color:var(--purple)}
.pay-copy{left:601px;top:2664px;font-family:"Jost",sans-serif;font-weight:500}
.pay-copy .a{font-size:32px;color:var(--purple);line-height:42px}
.pay-copy .b{font-size:38px;color:var(--teal);line-height:46px}
.arc-band{left:0;top:2779px;width:1200px;height:160px}

/* blog */
.blog-title{left:0;top:3016px;width:1200px;text-align:center;font-family:"Jost",sans-serif;font-weight:500;font-size:31px;color:var(--purple)}
.blog-sub{left:0;top:3075px;width:1200px;text-align:center;font-size:15px;color:var(--purple)}
.post{width:266px;height:460px;background:var(--white);border-radius:10px;box-shadow:0 2px 9px rgba(0,0,0,.16)}
.post .pic{position:absolute;left:-6px;top:0;width:266px;height:204px;border-radius:10px}
.post h3{position:absolute;left:0;top:230px;width:100%;text-align:center;font-family:"Jost",sans-serif;font-weight:400;font-size:18px;color:#111}
.post p{position:absolute;left:14px;top:272px;width:238px;text-align:center;font-size:12.5px;line-height:22px;color:#333}
.post .read{position:absolute;left:74px;top:377px;width:119px;height:52px;background:var(--purple);font-size:16px}

/* footer */
.footer{left:0;top:3660px;width:1200px;height:653px;background:var(--ink);color:var(--white)}
.footer > .waves{position:absolute;left:0;top:0}
.chat{left:966px;top:168px;width:60px;height:60px;border-radius:50%;background:var(--teal);display:flex;align-items:center;justify-content:center}
.chat svg{display:block}
.footer .brand{left:172px;top:300px;font-size:42px}
.footer .social{left:172px;top:398px;gap:20px}
.footer .social span{width:32px;height:32px}
.links{font-family:"Jost",sans-serif;font-size:13px;line-height:34.5px}
.links.col1{left:484px;top:290px}
.links.col2{left:634px;top:290px}
.signup{left:808px;top:296px;font-family:"Jost",sans-serif;font-weight:500;font-size:17px;line-height:25px}
.email{left:808px;top:364px;width:218px;height:52px;background:var(--white);color:#222;font-size:12px;padding:19px 10px}
.subscribe{left:808px;top:426px;width:109px;height:49px;background:var(--teal);font-size:13px;font-family:"Jost",sans-serif;display:flex;align-items:center;justify-content:center}
.rule{left:172px;top:552px;width:854px;height:1px;background:var(--line)}
.copyright{left:0;top:595px;width:1200px;text-align:center;font-family:"Jost",sans-serif;font-size:13px}
</style>
</head>
<body>

<header>
  <div class="abs topbar">
    <span class="abs promo">"Free shipping on all orders $50 and over!"</span>
    <div class="abs social"><span></span><span></span><span></span><span></span></div>
  </div>
  <nav class="abs nav">
    <div class="abs brand">Bright Nook</div>
    <div class="abs menu">
      <a class="active">HOME</a><a>ABOUT</a><a>SHOP</a><a>OUR STORY</a><a>HAPPY BLOG</a><a>CONTACT</a>
    </div>
    <svg class="abs cart" width="44" height="46" viewBox="0 0 44 46" aria-label="Cart">
      <path d="M6 16 H38 L35 42 H9 Z" fill="none" stroke="#fff" stroke-width="3" stroke-linejoin="round"/>
      <path d="M15 20 V12 a7 7 0 0 1 14 0 V20" fill="none" stroke="#fff" stroke-width="3"/>
      <circle cx="36" cy="8" r="8" fill="#35bfc8"/>
      <text x="36" y="12" font-size="11" fill="#fff" text-anchor="middle" font-family="Jost,sans-serif">0</text>
    </svg>
  </nav>
</header>

<section class="abs hero">
  <svg width="1200" height="740" viewBox="0 0 1200 740">
    <defs>
      <linearGradient id="heroTone" x1="0" y1="0" x2="1" y2="1">
        <stop offset="0" stop-color="#c9c2b3"/>
        <stop offset=".45" stop-color="#f3ede4"/>
        <stop offset=".8" stop-color="#d9cfc4"/>
        <stop offset="1" stop-color="#a89e96"/>
      </linearGradient>
    </defs>
    <path d="M0 0 H1200 V555 Q600 845 0 555 Z" fill="url(#heroTone)" role="img" aria-label="Woman relaxing on a yoga mat with legs up the wall in a bright room"/>
    <path d="M42 601 Q600 879 1158 601 Q600 779 42 601 Z" fill="#35bfc8"/>
  </svg>
  <div class="abs hero-badge"></div>
  <h1 class="abs hero-title">Bright Nook</h1>
  <a class="abs btn shop">Shop Now</a>
  <div class="abs dots"><span></span><span></span><span></span></div>
</section>

<aside class="abs sale">
  <div class="abs thumb" role="img" aria-label="Flat lay of bath accessories and skincare"></div>
  <p class="abs">“50% off sale going on now! Because saving money also makes us happy”</p>
</aside>

<h2 class="abs key-title">THE KEY TO TOTAL BLISS IS NURTURING THE MIND,<br>BODY, AND SOUL</h2>

<section class="products">
  <div class="abs card" style="left:172px;top:1344px;width:243px;height:318px">
    <div class="pic" role="img" aria-label="Bar of handmade soap"></div>
    <div class="label" style="top:262px">NEMO ENIM IPSAM</div>
  </div>
  <div class="abs card" style="left:435px;top:1344px;width:243px;height:318px">
    <div class="pic" role="img" aria-label="Shea butter and shea nuts"></div>
    <div class="label" style="top:262px">NEMO ENIM IPSAM</div>
  </div>
  <div class="abs card" style="left:172px;top:1692px;width:243px;height:288px">
    <div class="pic" style="top:30px;height:170px" role="img" aria-label="Bowl of shea butter with nuts"></div>
    <div class="label" style="top:228px">NEMO ENIM IPSAM</div>
  </div>
  <div class="abs card" style="left:435px;top:1692px;width:243px;height:288px">
    <div class="pic" style="top:30px;height:170px" role="img" aria-label="Spa oils, towel and stones"></div>
    <div class="label" style="top:228px">NEMO ENIM IPSAM</div>
  </div>
  <div class="abs feature" style="left:696px;top:1344px;width:330px;height:370px;background:linear-gradient(160deg,#6f8f8a 0%,#b7a897 45%,#d9d2c6 70%,#6a5a50 100%)" role="img" aria-label="Smiling woman in a bathrobe holding a jar of body cream">
    <div class="copy" style="top:292px"><h3>NEMO ENIM IPSAM</h3><p>Nam libero tempore, cum soluta</p></div>
  </div>
  <div class="abs feature" style="left:696px;top:1738px;width:330px;height:242px;background:linear-gradient(160deg,#4f7f7a 0%,#6f9690 50%,#b9ada0 100%)" role="img" aria-label="Woman in a bathrobe holding a flower">
    <div class="copy" style="top:165px"><h3>NEMO ENIM IPSAM</h3><p>Nam libero tempore, cum soluta</p></div>
  </div>
</section>

<section class="abs about">
  <h2 class="abs">ABOUT US</h2>
  <p class="abs">They say that home is where the heart is. But home is also where your mind and body reside. At Bright Nook we believe that home should be your place of Zen. A respite from the crazy world outside those walls. It is where you recharge your soul so you can approach each day with the focus and energy necessary to conquer the world.</p>
  <a class="abs btn tell">Tell Me More</a>
  <div class="abs pic" role="img" aria-label="Citrus, ginger, herbs and skincare bottles arranged on a table"></div>
</section>

<section class="pay">
  <div class="abs pay-name">Easeway</div>
  <div class="abs pay-copy"><div class="a">Don’t sweat it.</div><div class="b">You can pay later</div></div>
  <svg class="abs arc-band" viewBox="0 0 1200 160">
    <path d="M42 10 Q600 288 1158 10 Q600 188 42 10 Z" fill="#35bfc8"/>
  </svg>
</section>

<section class="blog">
  <h2 class="abs blog-title">THE HAPPY BLOG</h2>
  <p class="abs blog-sub">Food for the mind, tips for the body and exercises for the soul.</p>

  <article class="abs post" style="left:178px;top:3152px">
    <div class="pic" style="background:linear-gradient(150deg,#5d7a4e,#b98a7a 50%,#d8c9bd)" role="img" aria-label="Woman relaxing in a rose petal bath"></div>
    <h3>NEMO ENIM IPSAM</h3>
    <p>Nam libero tempore, cum soluta nobis est eligendi optio cumque nihil impedit quo minus id quod maxime placeat facere possimus.</p>
    <a class="btn read">Read More</a>
  </article>
  <article class="abs post" style="left:469px;top:3152px">
    <div class="pic" style="background:linear-gradient(150deg,#d9cfc3,#e8a45a 40%,#6b3a4a 70%,#e3dbd1)" role="img" aria-label="Bowls of citrus and berries on a bed"></div>
    <h3>NEMO ENIM IPSAM</h3>
    <p>Nam libero tempore, cum soluta nobis est eligendi optio cumque nihil impedit quo minus id quod maxime placeat facere possimus.</p>
    <a class="btn read">Read More</a>
  </article>
  <article class="abs post" style="left:760px;top:3152px">
    <div class="pic" style="background:linear-gradient(150deg,#c9b9a4,#8a6a52 45%,#3d4a63 80%)" role="img" aria-label="Woman exercising with dumbbells at home"></div>
    <h3>NEMO ENIM IPSAM</h3>
    <p>Nam libero tempore, cum soluta nobis est eligendi optio cumque nihil impedit quo minus id quod maxime placeat facere possimus.</p>
    <a class="btn read">Read More</a>
  </article>
</section>

<footer class="abs footer">
  <svg class="waves" width="1200" height="200" viewBox="0 0 1200 200">
    <path d="M0 0 H1200 Q600 260 0 0 Z" fill="#fff"/>
    <path d="M42 31 Q600 349 1158 31 Q600 249 42 31 Z" fill="#35bfc8"/>
  </svg>
  <div class="abs chat">
    <svg width="30" height="26" viewBox="0 0 30 26" aria-label="Chat">
      <path d="M3 3 H27 V18 H12 L6 23 V18 H3 Z" fill="none" stroke="#fff" stroke-width="2.5" stroke-linejoin="round"/>
      <circle cx="10" cy="10.5" r="1.6" fill="#fff"/><circle cx="15" cy="10.5" r="1.6" fill="#fff"/><circle cx="20" cy="10.5" r="1.6" fill="#fff"/>
    </svg>
  </div>
  <div class="abs brand">Bright Nook</div>
  <div class="abs social"><span></span><span></span><span></span><span></span></div>
  <div class="abs links col1"><div>HOME</div><div>ABOUT</div><div>SHOP</div><div>OUR STORY</div><div>HAPPY BLOG</div><div>CONTACT</div></div>
  <div class="abs links col2"><div>OUR STORY</div><div>CAREERS</div><div>PRIVACY POLICY</div><div>TERMS AND</div><div>CONDITIONS</div></div>
  <div class="abs signup">SIGN UP FOR OUR<br>NEWSLETTER</div>
  <div class="abs email">Email Address</div>
  <div class="abs subscribe">SUBSCRIBE</div>
  <div class="abs rule"></div>
  <div class="abs copyright">Copyrights © 2021 Bright Nook. All Rights reserved.</div>
</footer>

</body>
</html>
```